BuildLinkHub.com Full Stationery Design

Business Card will have all info on it. Letterhead will not have name, title or mobile number. Keep general feeling very clean, using colors from the logo as accents.
Name:Dale Marchetti
Title:President
Phone: 1-800-555-0142
Cell: 306-555-0187
email: dale@buildlinkhub.example
website: www.buildlinkhub.example
Address:
PO Box 947
Maplecrest, AB
S0J2T0

Target Market(s)

Construction Business owners

Industry/Entity Type

Business

Contact Information for Business Card

Name:Dale Marchetti
Title:President
Phone: 1-800-555-0142
Cell: 306-555-0187
Address:
PO Box 947
Maplecrest, AB
S0J2T0

Font styles to use
Sans Serif

Requirements
Must have
• Clean look
Should not have
• Images or cartoon type characters or tools

```html
<!DOCTYPE html>
<html lang="en">
<head>
<meta charset="utf-8">
<title>BuildLinkHub.com Business Card</title>
<link rel="stylesheet" href="https://fonts.googleapis.com/css2?family=Open+Sans:wght@700&family=Questrial&display=swap">
<style>
  :root{
    --backdrop:#e9e7e4;
    --white:#ffffff;
    --slate:#48586a;
    --slate-line:#566170;
    --orange:#f68b24;
    --red:#e8262e;
  }
  html,body{margin:0;padding:0;width:1200px;height:987px;overflow:hidden;background:var(--backdrop);}
  .stage{position:relative;width:1200px;height:987px;}
  .card{position:absolute;left:293px;width:615px;height:352px;overflow:hidden;}
  .card--front{top:130px;background:linear-gradient(180deg,var(--orange) 0%,var(--red) 100%);}
  .card--back{top:506px;background:var(--slate);}
  .front-shape{position:absolute;inset:0;width:100%;height:100%;}
  .brand{position:absolute;display:flex;align-items:center;font-family:"Questrial",sans-serif;white-space:nowrap;}
  .brand__mark{display:block;background:var(--orange);}
  .brand--front{left:35px;top:155px;font-size:23px;color:var(--slate);gap:8px;}
  .brand--front .brand__mark{width:20px;height:20px;}
  .brand--back{left:0;right:0;top:152px;justify-content:center;font-size:36px;color:var(--white);gap:12px;}
  .brand--back .brand__mark{width:30px;height:30px;}
  .identity{position:absolute;right:29px;top:40px;text-align:right;color:var(--white);}
  .identity__name{font-family:"Open Sans",sans-serif;font-weight:700;font-size:21px;line-height:24px;margin:0;}
  .identity__title{font-family:"Questrial",sans-serif;font-size:16px;line-height:20px;margin:0;}
  .address{position:absolute;right:29px;top:174px;text-align:right;color:var(--white);font-family:"Questrial",sans-serif;font-size:15px;line-height:21px;margin:0;font-style:normal;}
  .contacts{position:absolute;right:29px;top:224px;margin:0;padding:0;list-style:none;color:var(--white);font-family:"Questrial",sans-serif;font-size:15px;}
  .contacts li{display:flex;justify-content:flex-end;align-items:center;gap:6px;height:23.5px;white-space:nowrap;}
  .contacts svg{width:15px;height:15px;flex:none;}
  .back-web{position:absolute;left:0;right:0;top:290px;text-align:center;color:var(--white);font-family:"Questrial",sans-serif;font-size:16px;}
</style>
</head>
<body>
<div class="stage">
  <section class="card card--front">
    <svg class="front-shape" viewBox="0 0 525 300" preserveAspectRatio="none" aria-hidden="true">
      <polygon points="0,0 140,0 269,70 269,230 140,300 0,300" fill="var(--slate-line)"/>
      <polygon points="0,0 133,0 262,71 262,229 133,300 0,300" fill="var(--white)"/>
      <polygon points="133,0 137,0 265,71 265,229 137,300 133,300 262,229 262,71" fill="var(--white)"/>
    </svg>
    <div class="brand brand--front"><span class="brand__mark"></span>BuildLinkHub.com</div>
    <div class="identity">
      <p class="identity__name">Dale Marchetti</p>
      <p class="identity__title">President</p>
    </div>
    <address class="address">PO Box 947<br>Maplecrest, AB, S0J2T0</address>
    <ul class="contacts">
      <li>1-800-555-0142
        <svg viewBox="0 0 16 16" aria-hidden="true"><path fill="#fff" d="M3.6 1.2l2.3 2.6-1.3 1.9c.9 2 2.5 3.6 4.5 4.6l1.9-1.3 2.7 2.2-1.2 2.6C7 13.6 2.4 9 1.2 2.6z"/></svg></li>
      <li>306-555-0187
        <svg viewBox="0 0 16 16" aria-hidden="true"><rect x="4" y="1" width="8" height="14" rx="1.2" fill="none" stroke="#fff" stroke-width="1.6"/><rect x="7" y="12" width="2" height="1.4" fill="#fff"/></svg></li>
      <li>dale@buildlinkhub.example
        <svg viewBox="0 0 16 16" aria-hidden="true"><rect x="1.5" y="4" width="13" height="9" fill="#fff"/><path d="M1.5 4l6.5 5 6.5-5" fill="none" stroke="var(--red)" stroke-width="1"/></svg></li>
      <li>www.buildlinkhub.example
        <svg viewBox="0 0 16 16" aria-hidden="true"><circle cx="8" cy="8" r="6.5" fill="#fff"/><path d="M8 1.5v13M1.5 8h13M8 1.5c-3 3.5-3 9.5 0 13M8 1.5c3 3.5 3 9.5 0 13" fill="none" stroke="var(--red)" stroke-width=".9"/></svg></li>
    </ul>
  </section>

  <section class="card card--back">
    <div class="brand brand--back"><span class="brand__mark"></span>BuildLinkHub.com</div>
    <div class="back-web">www.buildlinkhub.example</div>
  </section>
</div>
</body>
</html>
```